Laser Tattoo Removal Business Cards

We are looking for a professional business card design for a laser tattoo removal business. Ideally looking for a black business card design. The name of the business is Brightline Tattoo Removal. We place our cards at local tattoo shops so we ideally are looking for something trendy/edgy to draw both male and female clientele in.

Target Market(s)

Male/Female ages 18-60

Contact Information for Business Card

black background ideally.. hoping to stay within greys, whites and black

Font styles to use
Serif
Sans Serif

Colors
121212
a9a9a9
5c5c5c
f5f5f5
ffffff
7f7f7f
606060
848484
9d9d9d

Requirements
Must have
• Employee Info:
• Melissa Thornbury
• Chief Executive Offer
• m: 919.537.2846
• w: 919.362.4178
• f: 919.685.3907
• mthornbury@brightlinetattooremoval.example
• Address:
• 4615 Oakmere Pkwy, Suite 210
• Raleigh, NC 27654
• Website:
• www.brightlinetattooremoval.example
Nice to have
• Myabe business name on back or logo on back and employee info on the front

```html
<!DOCTYPE html>
<html lang="en">
<head>
<meta charset="utf-8">
<title>Brightline Tattoo Removal – Business Cards</title>
<link rel="stylesheet" href="https://fonts.googleapis.com/css2?family=Josefin+Sans:wght@400;600&family=Raleway:wght@300;400&display=swap">
<style>
  :root {
    --ink: #121212;
    --silver: #a9a9a9;
    --mid: #5c5c5c;
    --paper: #ffffff;
    --paper-soft: #f5f5f5;
    --rule: #9d9d9d;
    --stage: #2b2b2b;
  }
  * { box-sizing: border-box; margin: 0; padding: 0; }
  html, body { width: 1200px; height: 900px; overflow: hidden; }
  body { background: var(--stage); position: relative; font-family: "Raleway", sans-serif; }

  .card {
    position: absolute;
    width: 600px;
    height: 343px;
    border-radius: 14px;
    overflow: hidden;
  }

  /* Front: black card with wordmark */
  .card-front {
    left: 80px; top: 70px;
    background: var(--ink);
    display: flex; flex-direction: column; align-items: center; justify-content: center;
  }
  .wordmark {
    font-family: "Josefin Sans", sans-serif;
    font-weight: 600;
    text-align: center;
    text-transform: uppercase;
    line-height: 1;
  }
  .card-front .wordmark { color: var(--silver); }
  .wordmark-name { display: block; font-size: 64px; letter-spacing: 4px; }
  .wordmark-sub { display: block; font-size: 22px; letter-spacing: 6px; margin-top: 16px; }
  .card-front .website {
    position: absolute; bottom: 34px; left: 0; right: 0;
    text-align: center;
    font-family: "Josefin Sans", sans-serif; font-weight: 600;
    color: var(--paper); font-size: 15px; letter-spacing: 2.5px;
  }

  /* Back: white card with band and contact list */
  .card-back {
    left: 520px; top: 487px;
    background: var(--paper);
  }
  .card-back .brand {
    height: 108px;
    display: flex; align-items: center; justify-content: flex-end;
    padding-right: 54px;
  }
  .card-back .wordmark { color: var(--ink); }
  .card-back .wordmark-name { font-size: 50px; }
  .card-back .wordmark-sub { font-size: 17px; margin-top: 10px; }

  .name-band {
    height: 56px;
    background: var(--ink);
    color: var(--paper);
    display: flex; flex-direction: column; justify-content: center;
    padding-left: 250px;
  }
  .person-name { font-size: 20px; letter-spacing: 1px; text-transform: uppercase; font-weight: 400; }
  .person-title { font-size: 15px; font-weight: 300; margin-top: 2px; }

  .contact-list { list-style: none; padding: 10px 40px 0 36px; }
  .contact-item {
    display: flex; align-items: center;
    height: 32px;
  }
  .contact-icon {
    width: 24px; height: 24px;
    background: var(--ink);
    flex: none;
    display: flex; align-items: center; justify-content: center;
  }
  .contact-icon svg { width: 15px; height: 15px; }
  .contact-text {
    margin-left: 16px;
    flex: 1;
    font-size: 14px;
    color: var(--ink);
    letter-spacing: 0.5px;
    white-space: nowrap;
    border-bottom: 2px dotted var(--rule);
    padding-bottom: 3px;
  }
</style>
</head>
<body>

  <section class="card card-front" aria-label="Card front">
    <div class="wordmark">
      <span class="wordmark-name">Brightline</span>
      <span class="wordmark-sub">Tattoo Removal</span>
    </div>
    <p class="website">www.brightlinetattooremoval.example</p>
  </section>

  <section class="card card-back" aria-label="Card back">
    <div class="brand">
      <div class="wordmark">
        <span class="wordmark-name">Brightline</span>
        <span class="wordmark-sub">Tattoo Removal</span>
      </div>
    </div>

    <div class="name-band">
      <p class="person-name">Melissa Thornbury</p>
      <p class="person-title">Chief Executive Offer</p>
    </div>

    <ul class="contact-list">
      <li class="contact-item">
        <span class="contact-icon">
          <svg viewBox="0 0 16 16" aria-hidden="true"><rect x="2" y="7" width="12" height="7" rx="1" fill="#fff"/><path d="M1 6c2-3 12-3 14 0v1h-3V5.5H4V7H1z" fill="#fff"/></svg>
        </span>
        <span class="contact-text">919.537.2846</span>
      </li>
      <li class="contact-item">
        <span class="contact-icon">
          <svg viewBox="0 0 16 16" aria-hidden="true"><path d="M4 1.5l2.2 3-1.4 1.6c.8 1.8 2.3 3.3 4.1 4.1l1.6-1.4 3 2.2-1.3 2.5C7 13 3 9 1.5 2.8z" fill="#fff"/></svg>
        </span>
        <span class="contact-text">919.362.4178</span>
      </li>
      <li class="contact-item">
        <span class="contact-icon">
          <svg viewBox="0 0 16 16" aria-hidden="true"><rect x="4" y="1.5" width="8" height="4" fill="#fff"/><rect x="1.5" y="6" width="13" height="6" rx="1" fill="#fff"/><rect x="4" y="10" width="8" height="4.5" fill="#fff" stroke="#121212" stroke-width="1"/></svg>
        </span>
        <span class="contact-text">919.685.3907</span>
      </li>
      <li class="contact-item">
        <span class="contact-icon">
          <svg viewBox="0 0 16 16" aria-hidden="true"><rect x="1.5" y="3.5" width="13" height="9" fill="none" stroke="#fff" stroke-width="1.4"/><path d="M1.5 3.5L8 9l6.5-5.5" fill="none" stroke="#fff" stroke-width="1.4"/></svg>
        </span>
        <span class="contact-text">mthornbury@brightlinetattooremoval.example</span>
      </li>
      <li class="contact-item">
        <span class="contact-icon">
          <svg viewBox="0 0 16 16" aria-hidden="true"><path d="M8 1a5 5 0 0 0-5 5c0 3.5 5 9 5 9s5-5.5 5-9a5 5 0 0 0-5-5z" fill="#fff"/><circle cx="8" cy="6" r="1.8" fill="#121212"/></svg>
        </span>
        <span class="contact-text">4615 Oakmere Pkwy, Suite 210, Raleigh, NC 27654</span>
      </li>
    </ul>
  </section>

</body>
</html>
```